accomplished personal trainer, former elite gymnast from Russia, highly professional and experienced

Established Fitness trainer in California requires a new web site to attract personal clients and build her group exercise classes.

Here is an example of another fitness trainer's site that I really liked the technology:
http://www.tedvorlam.com

Below I have inserted my current web site: www.quelbornfitnesslodi.com
You can use this web site for the principal content, such as my background and qualifications.

Target Market(s)

Anyone who wants to improve their fitness levels and wellness in general. Anyone who needs directions and instruction on how to exercise. I can train anyone from elite athlete to a disabled person.

Industry/Entity Type

Fitness

Coding

Coded - Design and coding required

Number of Pages Required

5+ page

Font styles to use
Sans Serif

Requirements
Must have
• Easy to navigate main info about me, location, services, contact, benefits of using my services.
• Would be great to create unique representation of me as a trainer and a person, using new technologies and new ideas. Make it different from the other websites. Having its own character. Not too complicated and heavy with information, but an eye catching, useful and fun to navigate.
Nice to have
• new technology, easy access to information, the idea of enjoyment of life, lightness about achieving any goal, spiritual wisdom, unique design. I am planning to insert educational videos, advise, maybe jokes. Sign in, shopping cart, logo, should be easy for me to make changes in content.
Should not have
• cliché, outdated technology, too complicated,

```html
<!DOCTYPE html>
<html lang="en">
<head>
<meta charset="utf-8">
<title>Quelborn Fitness Lodi</title>
<link href="https://fonts.googleapis.com/css2?family=Mulish:wght@400;600;700&family=Open+Sans:wght@400;600&display=swap" rel="stylesheet">
<style>
:root{
  --ink:#1d1d1d;
  --grey-text:#6e6e6e;
  --soft-text:#8a8a8a;
  --band:#efefef;
  --white:#ffffff;
  --accent:#ec7c14;
  --dark:#2a2a2a;
  --button-dark:#4a4a4a;
  --grass:#6f9a3c;
  --leaf:#3d5a2a;
}
*{margin:0;padding:0;box-sizing:border-box}
html,body{width:1200px;height:2975px;overflow:hidden}
body{font-family:"Open Sans",Arial,sans-serif;color:var(--ink);background:var(--white);position:relative}
.heading{font-family:"Mulish",Arial,sans-serif}

.site-header{height:107px;display:flex;align-items:center;padding:0 107px;background:var(--white)}
.brand{font-family:"Mulish",Arial,sans-serif;font-weight:700;font-size:21px;letter-spacing:1.5px;color:var(--ink)}
.main-nav{margin-left:auto;display:flex;height:107px;align-items:center}
.main-nav a{font-family:"Mulish",Arial,sans-serif;font-size:14px;font-weight:600;color:#333;text-decoration:none;display:flex;align-items:center;height:107px}
.main-nav .sep{width:22px;height:107px;margin:0 14px}

.hero{height:491px;position:relative;background:linear-gradient(160deg,#3f6a2c 0%,#7aa443 45%,#a4c268 70%,#6e9a3a 100%)}
.hero-text{position:absolute;left:0;right:0;top:160px;text-align:center;font-family:"Mulish",Arial,sans-serif;font-weight:600;font-size:66px;line-height:72px;letter-spacing:1px}
.hero-text .outline{color:transparent;-webkit-text-stroke:2px var(--white)}
.hero-text .solid{color:var(--white);text-shadow:0 2px 6px rgba(0,0,0,.35)}
.hero-dots{position:absolute;top:551px;left:0;right:0;display:flex;justify-content:center;gap:6px;top:auto;bottom:24px}
.hero-dots span{width:18px;height:18px;border-radius:50%;background:var(--white)}
.hero-dots span.active{background:transparent;border:2px solid var(--white)}

.testimonial{height:234px;background:var(--band);position:relative;display:flex;align-items:center;justify-content:center}
.testimonial p{width:880px;text-align:center;font-family:"Mulish",Arial,sans-serif;font-size:21px;line-height:30px;color:var(--soft-text)}
.testimonial .pointer{position:absolute;bottom:-26px;left:558px;width:56px;height:28px}

.about{height:463px;position:relative}
.about-photo{position:absolute;left:107px;top:66px;width:326px;height:340px;border-radius:16px;background:linear-gradient(170deg,#557a35 0%,#86aa4f 55%,#b7c98a 100%)}
.about-body{position:absolute;left:480px;top:90px;width:640px}
.about-body h2{font-family:"Mulish",Arial,sans-serif;font-weight:600;font-size:34px;color:#555;margin-bottom:22px}
.about-body p{font-size:13.5px;line-height:27px;color:var(--grey-text);margin-bottom:24px}
.btn-dark{display:inline-block;background:var(--button-dark);color:var(--white);font-family:"Mulish",Arial,sans-serif;font-size:14px;font-weight:600;padding:13px 34px;outline:2px solid var(--button-dark);border:2px solid #bdbdbd;outline-offset:0;text-decoration:none}

.services{height:427px;background:var(--band);position:relative}
.service{position:absolute;top:30px;width:480px}
.service.personal{left:104px}
.service.group{left:618px}
.service .hex{position:absolute;left:0;top:0;width:190px;height:218px}
.service .icon{position:absolute;left:56px;top:60px;width:60px;height:60px}
.service h3{position:absolute;left:56px;top:138px;font-family:"Mulish",Arial,sans-serif;font-weight:600;font-size:25px;color:#333}
.service p{position:absolute;left:56px;top:184px;width:440px;font-size:13.5px;line-height:26px;color:var(--grey-text)}
.btn-light{position:absolute;left:56px;top:308px;background:var(--white);border:2px solid #cfcfcf;font-family:"Mulish",Arial,sans-serif;font-size:14px;font-weight:600;color:#333;padding:12px 30px;text-decoration:none}

.videos{height:393px;position:relative;background:linear-gradient(180deg,#2d3a22 0%,#3e5030 50%,#262b20 100%)}
.videos h2{position:absolute;top:36px;left:0;right:0;text-align:center;font-family:"Mulish",Arial,sans-serif;font-weight:600;font-size:30px;color:var(--white)}
.video-card{position:absolute;top:100px;width:312px;height:208px;border:4px solid var(--white)}
.video-card:nth-of-type(1){left:107px;background:linear-gradient(160deg,#6f9a3c,#a9c27a)}
.video-card:nth-of-type(2){left:443px;background:linear-gradient(160deg,#5d8a32,#b0c46a)}
.video-card:nth-of-type(3){left:780px;background:linear-gradient(160deg,#4e7a34,#8db65a)}
.video-card svg{position:absolute;left:50%;top:50%;width:56px;height:56px;margin:-28px 0 0 -28px}

.news{height:335px;position:relative}
.news h2{position:absolute;left:109px;top:60px;font-family:"Mulish",Arial,sans-serif;font-weight:700;font-size:30px;color:var(--accent)}
.news-item{position:absolute;top:128px;width:300px}
.news-item:nth-of-type(1){left:109px}
.news-item:nth-of-type(2){left:454px}
.news-item:nth-of-type(3){left:799px}
.news-item h3{font-family:"Mulish",Arial,sans-serif;font-weight:600;font-size:18px;line-height:25px;color:#222;margin-bottom:6px}
.news-item p{font-size:13px;line-height:23px;color:var(--grey-text)}
.news-item a{display:block;margin-top:6px;font-size:13px;font-weight:600;color:var(--accent);text-decoration:none}

.newsletter{height:375px;position:relative;background:linear-gradient(100deg,#263a1e 0%,#456233 45%,#7b9a58 75%,#b7b77c 100%)}
.newsletter h2{position:absolute;left:113px;top:68px;font-family:"Mulish",Arial,sans-serif;font-weight:600;font-size:29px;color:var(--white)}
.newsletter .lead{position:absolute;left:113px;top:114px;font-size:15px;color:#e8e8e8}
.field{position:absolute;left:111px;width:360px;height:44px;background:var(--white);font-size:13px;color:#777;padding:13px 16px}
.field.name{top:148px}
.field.email{top:200px}
.btn-subscribe{position:absolute;left:111px;top:260px;width:148px;height:48px;background:#555;border:3px solid #999;color:var(--white);font-family:"Mulish",Arial,sans-serif;font-weight:600;font-size:14px;display:flex;align-items:center;justify-content:center}

.site-footer{height:150px;background:var(--dark);position:relative}
.footer-nav{position:absolute;left:116px;top:40px;display:flex;gap:30px}
.footer-nav a{font-family:"Mulish",Arial,sans-serif;font-weight:600;font-size:14px;color:var(--white);text-decoration:none}
.legal{position:absolute;left:116px;top:74px;font-size:11px;color:#bdbdbd}
.social{position:absolute;left:932px;top:32px;display:flex;gap:6px}
.social span{width:32px;height:32px;border:2px solid var(--white);border-radius:50%}
</style>
</head>
<body>

<header class="site-header">
  <div class="brand">QUELBORN FITNESS LODI</div>
  <nav class="main-nav">
    <a href="#">GROUP CLASSES</a>
    <svg class="sep" viewBox="0 0 22 107"><path d="M2 0 L20 53 L2 107" fill="none" stroke="#e3e3e3" stroke-width="2"/></svg>
    <a href="#">PERSONAL TRAINING</a>
    <svg class="sep" viewBox="0 0 22 107"><path d="M2 0 L20 53 L2 107" fill="none" stroke="#e3e3e3" stroke-width="2"/></svg>
    <a href="#">ABOUT QUELBORN</a>
    <svg class="sep" viewBox="0 0 22 107"><path d="M2 0 L20 53 L2 107" fill="none" stroke="#e3e3e3" stroke-width="2"/></svg>
    <a href="#">BLOG</a>
    <svg class="sep" viewBox="0 0 22 107"><path d="M2 0 L20 53 L2 107" fill="none" stroke="#e3e3e3" stroke-width="2"/></svg>
    <a href="#">CONTACT</a>
  </nav>
</header>

<section class="hero" role="img" aria-label="Photo of the trainer doing a split stretch on the grass in a park">
  <div class="hero-text">
    <div class="outline">WELCOME</div>
    <div class="solid">FITNESS OUTDOORS</div>
  </div>
  <div class="hero-dots"><span class="active"></span><span></span><span></span><span></span></div>
</section>

<section class="testimonial">
  <p>I have known Marina for many years as a fitness trainer and workout class instructor. She is truly one of the very best in the business. Marina is extremely knowledgeable about human physiology and teaching. Her personality is professional, informative, and caring. She would always put “her all” into each of her classes.</p>
  <svg class="pointer" viewBox="0 0 56 28"><path d="M0 0 H56 L28 28 Z" fill="#efefef"/></svg>
</section>

<section class="about">
  <div class="about-photo" role="img" aria-label="Photo of the trainer kneeling on the grass in a pink top"></div>
  <div class="about-body">
    <h2>About Quelborn Fitness</h2>
    <p>Marina Velk is the owner of Quelborn Fitness. She was born and raised in Vologda, Russia where she was a competitive gymnast. Marina graduated from Kostrova Academy of Sport with a bachelor degree in Kinesiology and Sports Science. For more than 20 years, Marina has worked as choreographer, gymnastics coach, and fitness professional.</p>
    <p>Marina has a deep knowledge (theory and experience) in many aspects of wellness including spirituality, nutrition, rehabilitation and is working towards a Physical Therapist degree.</p>
    <a class="btn-dark" href="#">READ MORE</a>
  </div>
</section>

<section class="services">
  <div class="service personal">
    <svg class="hex" viewBox="0 0 190 218"><path d="M95 2 L188 56 L188 162 L95 216 L2 162 L2 56 Z" fill="none" stroke="#dcdcdc" stroke-width="2"/></svg>
    <svg class="icon" viewBox="0 0 60 60"><rect x="24" y="2" width="12" height="5" fill="#222"/><rect x="28" y="6" width="4" height="6" fill="#222"/><circle cx="30" cy="34" r="22" fill="none" stroke="#222" stroke-width="4"/><path d="M30 34 V18 A16 16 0 0 1 44 28 Z" fill="#222"/><line x1="46" y1="14" x2="50" y2="10" stroke="#222" stroke-width="4"/></svg>
    <h3>Personal Training</h3>
    <p>Private sessions will provide you with the motivation you need to reach your goals. As an NCFA certified trainer, Marina will make sure you're working out safely and keep the workouts fresh and exciting so you can achieve your goals.</p>
    <a class="btn-light" href="#">READ MORE</a>
  </div>
  <div class="service group">
    <svg class="hex" viewBox="0 0 190 218"><path d="M95 2 L188 56 L188 162 L95 216 L2 162 L2 56 Z" fill="none" stroke="#dcdcdc" stroke-width="2"/></svg>
    <svg class="icon" viewBox="0 0 60 60"><path d="M8 30 A12 12 0 1 0 30 26 L56 22 V12 L22 16 A12 12 0 0 0 8 30 Z" fill="none" stroke="#222" stroke-width="3.5" stroke-linejoin="round"/><circle cx="19" cy="30" r="4" fill="#222"/><rect x="40" y="8" width="8" height="6" fill="none" stroke="#222" stroke-width="2.5"/></svg>
    <h3>Group Classes</h3>
    <p>Quelborn Group Exercise classes are designed for people of all fitness levels. Quelborn's group classes take a holistic approach and make sure you work out in a balanced way that feeds your body and spirit.</p>
    <a class="btn-light" href="#">READ MORE</a>
  </div>
</section>

<section class="videos" role="img" aria-label="Dimmed photo of a group exercising outdoors under trees">
  <h2>Educational Videos</h2>
  <div class="video-card" role="img" aria-label="Video still of a stability ball exercise on the grass">
    <svg viewBox="0 0 56 56"><circle cx="28" cy="28" r="25" fill="none" stroke="#fff" stroke-width="3"/><path d="M22 16 L40 28 L22 40 Z" fill="none" stroke="#fff" stroke-width="3" stroke-linejoin="round"/></svg>
  </div>
  <div class="video-card" role="img" aria-label="Video still of a group class doing squats in a park">
    <svg viewBox="0 0 56 56"><circle cx="28" cy="28" r="25" fill="none" stroke="#fff" stroke-width="3"/><path d="M22 16 L40 28 L22 40 Z" fill="none" stroke="#fff" stroke-width="3" stroke-linejoin="round"/></svg>
  </div>
  <div class="video-card" role="img" aria-label="Video still of an assisted stretch under a tree">
    <svg viewBox="0 0 56 56"><circle cx="28" cy="28" r="25" fill="none" stroke="#fff" stroke-width="3"/><path d="M22 16 L40 28 L22 40 Z" fill="none" stroke="#fff" stroke-width="3" stroke-linejoin="round"/></svg>
  </div>
</section>

<section class="news">
  <h2>News &amp; Advices</h2>
  <article class="news-item">
    <h3>Morbi diam mauris viverra</h3>
    <p>in gravida eu mattis in ante Morbi eget arcu Morbi porta libero id ullamcorper nonummy nibh ligula pulvinar metus eget t placerat molestie Donec dictum lectus non</p>
    <a href="#">READ MORE</a>
  </article>
  <article class="news-item">
    <h3>Donec dictum lectus no</h3>
    <p>in gravida eu mattis in ante Morbi eget arcu Morbi porta libero id ullamcorper nonummy nibh ligula pulvinar metus eget molestie Donec dictum lectus non</p>
    <a href="#">READ MORE</a>
  </article>
  <article class="news-item">
    <h3>Cum sociis natoque penatibus et magnis dis parturient</h3>
    <p>Morbi porta libero id ullamcorper nonummy nibh ligula pulvinar metus molestie Donec dictum lectus non que habitant</p>
    <a href="#">READ MORE</a>
  </article>
</section>

<section class="newsletter" role="img" aria-label="Photo of the trainer stretching sideways in a park">
  <h2>Newsletter Subscribe</h2>
  <p class="lead">Sign up with your email address to receive the latest news and updates.</p>
  <div class="field name">Name</div>
  <div class="field email">Email address</div>
  <div class="btn-subscribe">SUBSCRIBE</div>
</section>

<footer class="site-footer">
  <nav class="footer-nav">
    <a href="#">GROUP CLASSES</a>
    <a href="#">PERSONAL TRAINING</a>
    <a href="#">ABOUT QUELBORN</a>
    <a href="#">BLOG</a>
    <a href="#">CONTACT</a>
  </nav>
  <p class="legal">© 2016 Company Name&nbsp; All right reserved&nbsp; Term of Use</p>
  <div class="social"><span></span><span></span><span></span><span></span></div>
</footer>

</body>
</html>
```